Meadowlark Property Review is a leading provider of residential appraisal and home inspection products in S

I need a business card/logo designed that obviously describes my business. We are a residential appraisal and home inspection company in Springfield, MO. We offer residential appraisals, home inspection, pest inspection and radon gas measurement. We have been in business for 18 years and hold state certified residential appraisal licenses and OBREX certified home inspection licenses. I have a logo that I really like and will attach, but would be open to new suggestions. I like more modern designs than traditional and would like a two sided card with our services, licenses and qualifications on the back.

```html
<!DOCTYPE html>
<html lang="en">
<head>
<meta charset="utf-8">
<title>Meadowlark Property Review – Business Card</title>
<link href="https://fonts.googleapis.com/css2?family=Open+Sans:wght@400;600;700&display=swap" rel="stylesheet">
<style>
  :root{
    --bg:#ece7df;
    --card:#ffffff;
    --ink:#1b1b1b;
    --brown:#9c7a52;
    --orange:#f39a2e;
    --shadow:rgba(60,40,20,.22);
  }
  *{box-sizing:border-box;margin:0;padding:0}
  html,body{width:1200px;height:892px;overflow:hidden}
  body{background:var(--bg);font-family:"Open Sans",Arial,sans-serif;color:var(--ink);position:relative}

  .card{position:absolute;width:580px;height:331px;background:var(--card);box-shadow:0 10px 24px var(--shadow)}
  .card--back{left:560px;top:70px}
  .card--front{left:60px;top:480px}

  .brand{position:absolute;display:flex;align-items:center;gap:10px;font-weight:700;color:var(--brown);font-size:25px;letter-spacing:.2px;white-space:nowrap}
  .brand__mark{width:16px;height:16px;background:var(--orange);flex:none}
  .card--back .brand{left:50%;top:44px;transform:translateX(-50%)}
  .card--front .brand{left:150px;top:40px}

  .services{position:absolute;list-style:none;font-size:17px;line-height:23px;color:var(--ink)}
  .services li{display:flex;align-items:center;gap:9px}
  .services svg{width:15px;height:13px;flex:none}
  .services--left{left:40px;top:118px}
  .services--right{left:330px;top:190px}

  .front-rule{position:absolute;left:80px;right:0;top:102px;height:3px;background:var(--ink)}
  .corner-art{position:absolute;left:0;bottom:0;width:170px;height:130px;background:linear-gradient(135deg,var(--brown),var(--orange))}

  .contact{position:absolute;right:30px;top:130px;display:flex;gap:14px}
  .contact__lines{text-align:right;font-weight:600;font-size:18px;line-height:25px}
  .contact__icons{display:flex;flex-direction:column;gap:9px;padding-top:6px}
  .icon{width:17px;height:17px;background:var(--brown);display:flex;align-items:center;justify-content:center}
  .icon svg{width:11px;height:11px;fill:none;stroke:#fff;stroke-width:1.6}
</style>
</head>
<body>

<svg width="0" height="0" style="position:absolute">
  <symbol id="tick" viewBox="0 0 15 13"><path d="M1 7 L5.5 11 L14 1.5" fill="none" stroke="#f39a2e" stroke-width="2.6" stroke-linecap="round" stroke-linejoin="round"/></symbol>
</svg>

<section class="card card--back" aria-label="Card back: services">
  <div class="brand"><span class="brand__mark"></span>Meadowlark Property Review</div>
  <ul class="services services--left">
    <li><svg><use href="#tick"/></svg>home inspection</li>
    <li><svg><use href="#tick"/></svg>property inspection</li>
    <li><svg><use href="#tick"/></svg>residential appraisal</li>
    <li><svg><use href="#tick"/></svg>termite inspection</li>
    <li><svg><use href="#tick"/></svg>radon gas measurement</li>
    <li><svg><use href="#tick"/></svg>pre purchase inspection</li>
  </ul>
  <ul class="services services--right">
    <li><svg><use href="#tick"/></svg>thermal imaging</li>
    <li><svg><use href="#tick"/></svg>mechanical inspection</li>
    <li><svg><use href="#tick"/></svg>tax appeal</li>
    <li><svg><use href="#tick"/></svg>asset evaluation</li>
    <li><svg><use href="#tick"/></svg>energy audits</li>
  </ul>
</section>

<section class="card card--front" aria-label="Card front: contact details">
  <div class="brand"><span class="brand__mark"></span>Meadowlark Property Review</div>
  <div class="front-rule"></div>
  <div class="corner-art" role="img" aria-label="Decorative brand graphic in brown and orange"></div>
  <div class="contact">
    <div class="contact__lines">
      <p>417-555-0142</p>
      <p>417-555-0178</p>
      <p>417-555-0163</p>
      <p>info@meadowlarkreview.com</p>
      <p>Meadowlark Property Review</p>
      <p>480 E Larkspur Road; Suite B</p>
      <p>Springfield, MO&nbsp; 65810</p>
    </div>
    <div class="contact__icons">
      <span class="icon"><svg viewBox="0 0 12 12"><rect x="3.5" y="1" width="5" height="10" rx="1"/></svg></span>
      <span class="icon"><svg viewBox="0 0 12 12"><path d="M2 2 L4.5 2 L5.5 4.5 L4 5.5 Q5 7.5 6.5 8 L7.5 6.5 L10 7.5 L10 10 Q4 10 2 2 Z"/></svg></span>
      <span class="icon"><svg viewBox="0 0 12 12"><rect x="1.5" y="4" width="9" height="6"/><rect x="3.5" y="1.5" width="5" height="2.5"/></svg></span>
      <span class="icon"><svg viewBox="0 0 12 12"><rect x="1.5" y="3" width="9" height="6.5"/><path d="M1.5 3 L6 7 L10.5 3"/></svg></span>
      <span class="icon"><svg viewBox="0 0 12 12"><path d="M6 11 Q2 6.5 2 4.5 A4 4 0 0 1 10 4.5 Q10 6.5 6 11 Z"/><circle cx="6" cy="4.5" r="1.2"/></svg></span>
    </div>
  </div>
</section>

</body>
</html>
```